Business card design for a teacher - double sided, sleek design.

My name is Lina and I am an online Arabic language teacher. I am looking for a beautiful business card design for my online teaching business.

The cards will be printed in 85mm x 55mm size.
The card can be either portrait or landscape.

The design should contain my logo on one side and information on the other.

The design needs to be clean and modern. Use of subtle Arabic geometric patterns would be nice. Icons for the social media information on the card should also match the design theme.

My logo font is Consolas, which is a Monospace font.

Business card design should be delivered with editable PSD or EPS files in the handover.

Thanks

Lina

----

Information on the back:

URL: www.speakwithnadia.net [this should stand out more than other details]
Email: info@speakwithnadia.net
Instagram: @speakwithnadia
Facebook: facebook.com/speakwithnadia
Skype: speakwithnadia

My brand colours are shown in the logo attached. These are:
- Teal green - 4DC9C1
- Mango yellow - FFD600

Target Market(s)

- Young professionals
- Expatriates
- Women and Men

Industry/Entity Type

Education

Contact Information for Business Card

Information on the back:

Skype: speakwithnadia

- Teal green - 4DC9C1
- Mango yellow - FFD600

Font styles to use
Other font styles liked:
• Any font complimentary to my logo font which is a Monospace font called Consolas.

Colors

Designer to choose colors to be used in the design.

Requirements
Must have
• - Aesthetically pleasing look
• - Complimentary design with existing logo
Nice to have
• Arabic geometrical patterns

```html
<!DOCTYPE html>
<html lang="en">
<head>
<meta charset="utf-8">
<title>Speak with Nadia – Business Card</title>
<link href="https://fonts.googleapis.com/css2?family=Montserrat:wght@400;500;700&display=swap" rel="stylesheet">
<style>
  :root {
    --backdrop: #2a2a2a;
    --card: #151515;
    --card-edge: #232323;
    --emboss: #2e2e2e;
    --emboss-line: #3a3a3a;
    --foil: #c9c9c9;
    --foil-dim: #9a9a9a;
    --divider: #3b3b3b;
  }
  * { margin: 0; padding: 0; box-sizing: border-box; }
  html, body { width: 1200px; height: 900px; overflow: hidden; }
  body {
    background: var(--backdrop);
    font-family: "Montserrat", sans-serif;
    position: relative;
  }
  .card {
    position: absolute;
    left: 300px;
    width: 600px;
    height: 388px;
    background: var(--card);
    border: 1px solid var(--card-edge);
    border-radius: 3px;
    box-shadow: 0 18px 40px rgba(0,0,0,0.45);
  }
  .card--front { top: 50px; }
  .card--back { top: 462px; }

  .brand-square {
    position: absolute;
    border: 2px solid var(--emboss-line);
    background: var(--emboss);
  }
  .card--front .brand-square { left: 150px; top: 134px; width: 110px; height: 110px; }
  .brand-name {
    position: absolute;
    left: 282px;
    top: 168px;
    color: var(--foil);
    font-weight: 500;
    font-size: 34px;
    letter-spacing: 3px;
    line-height: 1.2;
    text-transform: uppercase;
  }

  .card--back .brand-square { left: 62px; top: 110px; width: 130px; height: 130px; }
  .divider {
    position: absolute;
    left: 232px;
    top: 88px;
    width: 1px;
    height: 200px;
    background: var(--divider);
  }
  .owner-name {
    position: absolute;
    left: 268px;
    top: 98px;
    color: var(--foil-dim);
    font-weight: 700;
    font-size: 34px;
    letter-spacing: 2px;
  }
  .contact-list {
    position: absolute;
    left: 268px;
    top: 160px;
    list-style: none;
  }
  .contact-list li {
    display: flex;
    align-items: center;
    gap: 12px;
    color: var(--foil);
    font-size: 19px;
    line-height: 27px;
    letter-spacing: 0.5px;
  }
  .contact-icon { width: 12px; height: 12px; flex: none; }
  .contact-list .contact--web { font-weight: 500; }
</style>
</head>
<body>
  <section class="card card--front">
    <div class="brand-square"></div>
    <div class="brand-name">Speak with Nadia</div>
  </section>

  <section class="card card--back">
    <div class="brand-square"></div>
    <div class="divider"></div>
    <div class="owner-name">LINA</div>
    <ul class="contact-list">
      <li><svg class="contact-icon" viewBox="0 0 12 12"><circle cx="6" cy="6" r="4.5" fill="none" stroke="#9a9a9a" stroke-width="1.4"/></svg>@speakwithnadia</li>
      <li><svg class="contact-icon" viewBox="0 0 12 12"><circle cx="6" cy="6" r="4.5" fill="none" stroke="#9a9a9a" stroke-width="1.4"/></svg>facebook.com/speakwithnadia</li>
      <li><svg class="contact-icon" viewBox="0 0 12 12"><circle cx="6" cy="6" r="4.5" fill="none" stroke="#9a9a9a" stroke-width="1.4"/></svg>speakwithnadia</li>
      <li><svg class="contact-icon" viewBox="0 0 12 12"><rect x="1" y="2.5" width="10" height="7" fill="none" stroke="#9a9a9a" stroke-width="1.2"/><polyline points="1,2.5 6,6.5 11,2.5" fill="none" stroke="#9a9a9a" stroke-width="1.2"/></svg>info@speakwithnadia.net</li>
      <li class="contact--web"><svg class="contact-icon" viewBox="0 0 12 12"><circle cx="6" cy="6" r="4.8" fill="none" stroke="#9a9a9a" stroke-width="1.2"/><ellipse cx="6" cy="6" rx="2" ry="4.8" fill="none" stroke="#9a9a9a" stroke-width="1"/><line x1="1.2" y1="6" x2="10.8" y2="6" stroke="#9a9a9a" stroke-width="1"/></svg>www.speakwithnadia.net</li>
    </ul>
  </section>
</body>
</html>
```